Company Website for Varnoth Signal, an open source data analytics company focused on relationship and li

I need a company/brand website for our new startup, Varnoth Signal LLC. We are a company focused on using life pattern analysis techniques, looking at relationships and how relationships, attributes, and activity cluster to infer aggregate information about individuals and groups. Our focus is on improving the digital advertising market.

We have a company logo which I will upload shortly.

Target Market(s)

Digital Advertising

Number of Pages Required

3 page

Font styles to use
Sans Serif

Requirements
Must have
• An main page, about us, contact page.
Nice to have
• Varnoth Signal relies on state of the art analytics applied to a the digital marketing space. While it is heavy in science, we also understand the art of influence. The website should have a scientific edge but also a flair that illustrates our focus on applying the hard science and analytics to influencing the behavior of people.

```html
<!DOCTYPE html>
<html lang="en">
<head>
<meta charset="utf-8">
<title>Varnoth Signal</title>
<link rel="stylesheet" href="https://fonts.googleapis.com/css2?family=Poppins:wght@400;500;600;700&family=Raleway:wght@400;500;600&display=swap">
<style>
:root{
  --blue:#1e8ed6;
  --blue-deep:#1570b8;
  --blue-soft:#cfe4f5;
  --orange:#f39a2b;
  --ink:#1d1d1d;
  --text:#3a3a3a;
  --grey:#9a9a9a;
  --line:#e3e3e3;
  --white:#ffffff;
  --beige:#f3ece2;
}
*{margin:0;padding:0;box-sizing:border-box}
html,body{width:1200px;height:3214px;overflow:hidden;background:var(--white)}
body{position:relative;font-family:"Raleway",sans-serif;color:var(--text)}
.abs{position:absolute}
.poppins{font-family:"Poppins",sans-serif}

/* header */
.site-header{position:absolute;left:0;top:0;width:1200px;height:103px;background:var(--white);box-shadow:0 2px 6px rgba(0,0,0,.08);z-index:2}
.brand{position:absolute;left:160px;top:26px;font-family:"Poppins",sans-serif;font-weight:700;font-size:30px;color:var(--blue);letter-spacing:.5px}
.call{position:absolute;right:160px;top:18px;font-family:"Poppins",sans-serif;font-size:21px;color:var(--ink);display:flex;align-items:center;gap:8px}
.call b{font-weight:400;color:var(--orange)}
.main-nav{position:absolute;right:160px;top:66px;display:flex;gap:22px;font-family:"Poppins",sans-serif;font-size:12.5px;color:var(--ink)}

/* hero */
.hero{position:absolute;left:0;top:103px;width:1200px;height:505px;background:linear-gradient(100deg,#2594dc,#1c86d0)}
.hero h1{position:absolute;left:162px;top:140px;font-family:"Poppins",sans-serif;font-weight:600;font-size:44px;color:var(--white)}
.hero p{position:absolute;left:162px;top:205px;width:380px;font-size:18px;line-height:28px;color:var(--white)}
.btn-outline{position:absolute;left:163px;top:309px;width:155px;height:48px;border:2px solid var(--white);color:var(--white);font-family:"Poppins",sans-serif;font-weight:500;font-size:18px;display:flex;align-items:center;justify-content:center}
.hero-art{position:absolute;left:620px;top:70px;width:400px;height:362px;border-radius:8px;background:linear-gradient(180deg,rgba(255,255,255,.35),rgba(255,255,255,.12))}
.dots{position:absolute;left:564px;top:460px;display:flex;gap:5px}
.dots i{width:13px;height:13px;border-radius:50%;background:var(--white);border:2px solid var(--white)}
.dots i.off{background:transparent}

/* section headings */
.sec-title{position:absolute;left:0;width:1200px;text-align:center;font-family:"Poppins",sans-serif;font-weight:600;font-size:27px;color:var(--ink)}
.sec-sub{position:absolute;left:310px;width:580px;text-align:center;font-size:11.5px;line-height:23px;color:var(--ink)}

/* feature cards */
.feature{position:absolute;top:795px;width:280px;height:350px;background:var(--white);box-shadow:0 3px 14px rgba(0,0,0,.14);text-align:center}
.feature .icon{position:absolute;left:82px;top:37px;width:116px;height:116px;border-radius:50%;background:var(--white);box-shadow:0 0 14px rgba(30,142,214,.25)}
.feature h3{position:absolute;top:192px;width:100%;font-family:"Poppins",sans-serif;font-weight:500;font-size:15px;color:var(--ink)}
.feature p{position:absolute;left:45px;top:225px;width:190px;font-size:11px;line-height:19px;color:var(--text)}

/* band */
.band{position:absolute;left:0;top:1228px;width:1200px;height:505px;background:linear-gradient(90deg,#2b2a33 0%,#4e4440 25%,#b88a5e 42%,#e7dac8 58%,var(--beige) 100%)}
.band h2{position:absolute;left:722px;top:125px;font-family:"Poppins",sans-serif;font-weight:600;font-size:29px;color:var(--ink)}
.band p{position:absolute;left:724px;top:188px;width:370px;font-size:11px;line-height:23.5px;color:var(--ink)}
.btn{position:absolute;background:var(--orange);color:var(--white);font-family:"Poppins",sans-serif;font-weight:500;border-radius:20px;display:flex;align-items:center;justify-content:center}

/* story cards */
.story{position:absolute;top:1940px;width:281px;height:410px;background:var(--white);border:1px solid var(--line);text-align:center}
.story .photo{position:absolute;left:0;top:0;width:279px;height:218px}
.story h3{position:absolute;top:240px;width:100%;font-family:"Poppins",sans-serif;font-weight:500;font-size:15.5px;color:var(--ink)}
.story p{position:absolute;left:30px;top:275px;width:220px;font-size:11px;line-height:20px;color:var(--text)}

/* analytics */
.analytics{position:absolute;left:0;top:2485px;width:1200px;height:385px;background:linear-gradient(100deg,#1d86d0,#1a74bd 60%,#166aae)}
.analytics h2{position:absolute;left:0;top:90px;width:1200px;text-align:center;font-family:"Poppins",sans-serif;font-weight:600;font-size:28px;color:var(--white)}
.analytics p{position:absolute;left:370px;top:136px;width:460px;text-align:center;font-size:17px;line-height:26px;color:#e6f2fb}

/* footer */
.footer-brand{position:absolute;left:160px;top:2975px;font-family:"Poppins",sans-serif;font-weight:600;font-size:34px;color:#a3a3a3;line-height:42px}
.f-col{position:absolute;top:2935px;font-family:"Poppins",sans-serif}
.f-col h4{font-weight:400;font-size:16.5px;color:var(--ink);margin-bottom:18px}
.f-col li{list-style:none;font-size:11px;color:var(--ink);line-height:25.5px}
.social{display:flex;gap:12px;margin-bottom:22px}
.social i{width:20px;height:20px;border-radius:50%;background:var(--ink)}
.copyright{position:absolute;left:0;top:3172px;width:1200px;text-align:center;font-family:"Poppins",sans-serif;font-size:11.5px;color:var(--ink)}
</style>
</head>
<body>

<header class="site-header">
  <div class="brand">Varnoth Signal</div>
  <div class="call">
    <svg width="20" height="20" viewBox="0 0 24 24"><path fill="#1d1d1d" d="M6.6 10.8a15.1 15.1 0 0 0 6.6 6.6l2.2-2.2c.3-.3.7-.4 1-.2 1.1.4 2.3.6 3.6.6.6 0 1 .4 1 1V20c0 .6-.4 1-1 1C10.6 21 3 13.4 3 4c0-.6.4-1 1-1h3.5c.6 0 1 .4 1 1 0 1.3.2 2.5.6 3.6.1.3 0 .7-.2 1z"/></svg>
    <span>Call Us :<b>0491570110</b></span>
  </div>
  <nav class="main-nav"><span>Home</span><span>About Us</span><span>Our Services</span><span>Data analytics</span><span>News</span><span>Careers</span><span>Contact Us</span></nav>
</header>

<section class="hero">
  <h1>VARNOTH SIGNAL</h1>
  <p>Lorem ipsum dolor sit amet, consectetur ipiscing elit, sed do eiusmod tempor incidi dunt ut labore et dolore magndolo.</p>
  <div class="btn-outline">READ MORE</div>
  <div class="hero-art" role="img" aria-label="Illustration of a team meeting around a table in front of a presentation board with charts"></div>
  <div class="dots"><i></i><i></i><i class="off"></i><i></i></div>
</section>

<h2 class="sec-title" style="top:672px">WELCOME TO VARNOTH SIGNAL</h2>
<p class="sec-sub" style="top:722px">Sed ut perspiciatis unde omnis iste natus error sit voluptatem accusantium doloremque laudantium, totam rem aperiam, eaque ipsa quae ab illo inventore veritatis et quasi architecto beatae vitae</p>

<article class="feature" style="left:160px">
  <div class="icon"><div role="img" aria-label="Icon of a group of people" style="position:absolute;left:30px;top:30px;width:56px;height:56px;border-radius:50%;background:linear-gradient(135deg,#fbd3a0,#bfe0f6)"></div></div>
  <h3>PEOPLE</h3>
  <p>Sed ut perspiciatis unde omnisiste lorenatus error sit voluptatem accusa ntiumdoloremque lumrem loreqp</p>
</article>
<article class="feature" style="left:460px">
  <div class="icon"><svg class="abs" style="left:28px;top:28px" width="60" height="60" viewBox="0 0 60 60" fill="none" stroke="#1e8ed6" stroke-width="2"><ellipse cx="30" cy="30" rx="26" ry="10"/><ellipse cx="30" cy="30" rx="26" ry="10" transform="rotate(60 30 30)"/><ellipse cx="30" cy="30" rx="26" ry="10" transform="rotate(-60 30 30)" stroke="#f39a2b"/><circle cx="30" cy="30" r="4" fill="#f39a2b" stroke="none"/></svg></div>
  <h3>SCIENCE</h3>
  <p>Sed ut perspiciatis unde omnisiste lorenatus error sit voluptatem accusa ntiumdoloremque lumrem loreqp</p>
</article>
<article class="feature" style="left:760px">
  <div class="icon"><svg class="abs" style="left:30px;top:28px" width="56" height="60" viewBox="0 0 56 60"><g fill="none" stroke="#1e8ed6" stroke-width="2"><rect x="6" y="34" width="7" height="18"/><rect x="18" y="28" width="7" height="24"/><rect x="30" y="22" width="7" height="30"/><rect x="42" y="16" width="7" height="36"/><path d="M2 54h52"/></g><path d="M6 26 L20 16 L30 20 L46 6" fill="none" stroke="#f39a2b" stroke-width="2.5"/><path d="M40 5h7v7" fill="none" stroke="#f39a2b" stroke-width="2.5"/></svg></div>
  <h3>ANALYTICS</h3>
  <p>Sed ut perspiciatis unde omnisiste lorenatus error sit voluptatem accusa ntiumdoloremque lumrem loreqp</p>
</article>

<section class="band">
  <div class="abs" role="img" aria-label="Photo of a group of friends standing together, silhouetted against a sunset field" style="left:0;top:0;width:600px;height:505px;background:linear-gradient(180deg,rgba(0,0,0,0) 0%,rgba(20,15,20,.35) 100%)"></div>
  <svg class="abs" style="left:0;top:0" width="1200" height="505" viewBox="0 0 1200 505">
    <polyline points="0,498 143,440 305,375 430,340 545,285 710,275 900,195 1075,140 1200,90" fill="none" stroke="#f7c88e" stroke-width="1.5"/>
    <g fill="#f39a2b"><circle cx="143" cy="440" r="5"/><circle cx="305" cy="375" r="5"/><circle cx="430" cy="340" r="5"/><circle cx="545" cy="285" r="5"/><circle cx="710" cy="275" r="5"/><circle cx="1075" cy="140" r="5"/></g>
  </svg>
  <h2>FINIBUS BONORUM</h2>
  <p>Lorem ipsum dolor sit amet, consectetur adipiscing eli, se dolore magna aliquat enim ad minim veniam, quis nostrud co laboris nisi ut aliqip elox ea commodo consequate ure din voluptateLorem ipsum dolor sit amet, consectetur adipiscing elit, sed do eiumod ure et dolore</p>
  <div class="btn" style="left:725px;top:325px;width:121px;height:38px;font-size:11.5px">READ MORE</div>
</section>

<h2 class="sec-title" style="top:1818px">FINIBUS BONORUM ET MALORUM</h2>
<p class="sec-sub" style="top:1863px;left:300px;width:600px">Sed ut perspiciatis unde omnis iste natus error sit voluptatem accusantium doloremque laudantium, totam rem aperiam, eaque ipsa quae ab illo inventore veritatis et quasi architecto beatae vitae dicta sunt expli.</p>

<article class="story" style="left:160px">
  <div class="photo" role="img" aria-label="Photo of hands holding a coffee cup and a tablet showing a social feed" style="background:linear-gradient(135deg,#3a2e28,#8a7b70 55%,#c9ccd2)"></div>
  <h3>SEDUT PERSPICIA</h3>
  <p>Sed ut perspiciatis unde omnis iste naus error sit voluptatem accusantium dolorem laudantium, totam rem aperiama.</p>
  <div class="btn" style="left:88px;top:347px;width:107px;height:33px;font-size:11px">READ MORE</div>
</article>
<article class="story" style="left:460px">
  <div class="photo" role="img" aria-label="Photo of a smiling woman looking at her phone" style="background:linear-gradient(135deg,#d8d2cc,#8a6a55 55%,#3a2a22)"></div>
  <h3>SEDUT PERSPICIA</h3>
  <p>Sed ut perspiciatis unde omnis iste naus error sit voluptatem accusantium dolorem laudantium, totam rem aperiama.</p>
  <div class="btn" style="left:88px;top:347px;width:107px;height:33px;font-size:11px">READ MORE</div>
</article>
<article class="story" style="left:757px">
  <div class="photo" role="img" aria-label="Photo of a large cheering crowd of people" style="background:linear-gradient(135deg,#4a4a52,#8c7c74 50%,#5a5660)"></div>
  <h3>SEDUT PERSPICIA</h3>
  <p>Sed ut perspiciatis unde omnis iste naus error sit voluptatem accusantium dolorem laudantium, totam rem aperiama.</p>
  <div class="btn" style="left:88px;top:347px;width:107px;height:33px;font-size:11px">READ MORE</div>
</article>

<svg class="abs" style="left:0;top:2340px" width="1200" height="146" viewBox="0 0 1200 146">
  <path d="M0 146 L0 110 C60 80 110 95 170 105 C230 75 300 60 360 100 C420 110 470 70 540 90 C600 70 660 95 720 85 C780 50 830 80 880 40 C900 -10 930 60 980 70 C1030 40 1080 60 1120 30 C1150 0 1180 20 1200 40 L1200 146Z" fill="#dbeaf7"/>
  <path d="M0 146 L0 125 C80 105 150 120 230 110 C300 100 360 125 430 115 C520 100 600 125 680 110 C760 95 820 110 900 90 C980 70 1060 95 1130 70 C1160 60 1185 70 1200 75 L1200 146Z" fill="#bcd8f0"/>
  <path d="M0 146 L0 138 C120 128 240 140 360 132 C480 124 600 138 720 128 C840 120 960 132 1080 118 C1140 112 1180 120 1200 122 L1200 146Z" fill="#9fc7ea"/>
</svg>

<section class="analytics">
  <svg class="abs" style="left:0;top:0" width="1200" height="385" viewBox="0 0 1200 385">
    <polyline points="0,385 143,343 306,335 453,280 610,270 712,205 873,205 970,125 1082,108 1178,57 1200,50" fill="none" stroke="#8cc4ec" stroke-width="1.5"/>
    <g fill="#f39a2b"><circle cx="143" cy="343" r="5"/><circle cx="453" cy="280" r="5"/><circle cx="712" cy="205" r="5"/><circle cx="873" cy="205" r="5"/><circle cx="970" cy="125" r="5"/><circle cx="1178" cy="57" r="5"/></g>
    <g fill="none" stroke="#cfe8fa" stroke-width="2"><circle cx="306" cy="335" r="5"/><circle cx="610" cy="270" r="5"/><circle cx="1082" cy="108" r="5"/></g>
    <text x="627" y="283" font-family="Poppins, sans-serif" font-size="11" fill="#ffffff">Relationship</text>
    <text x="885" y="217" font-family="Poppins, sans-serif" font-size="11" fill="#ffffff">Lifestyle behaviors</text>
  </svg>
  <h2>OUR DATA ANALYTICS</h2>
  <p>Sed ut perspiciatis unde omnis iste natus error sit atem accusantium doloremque laudantium, totam.</p>
</section>

<svg class="abs" style="left:0;top:3090px" width="1200" height="124" viewBox="0 0 1200 124">
  <path d="M0 124 L0 80 C150 40 300 70 450 60 C600 50 750 90 900 70 C1020 55 1120 75 1200 65 L1200 124Z" fill="#f4f7fb"/>
</svg>

<div class="footer-brand">Varnoth<br>Signal</div>
<div class="f-col" style="left:472px"><h4>Links</h4><ul><li>Sed uterspiciatis</li><li>Sed uerspiciatiem</li><li>Comnisteatusit</li><li>Perspiciatis unde</li><li>Sed uerspiciatiem</li></ul></div>
<div class="f-col" style="left:703px"><h4>Connect</h4><div class="social"><i></i><i></i><i></i><i></i></div><h4 style="margin-bottom:12px">Policies</h4><ul><li>Privacy</li><li>Complaint and Feedback</li></ul></div>
<div class="f-col" style="left:940px"><h4>Other Links</h4><ul><li>Sed uterspiciatis</li><li>Sed uerspiciatiem</li><li>Comnisteatusit</li><li>Perspiciatis unde</li><li>Sed uerspiciatiem</li></ul></div>
<div class="abs" style="left:440px;top:3135px;width:615px;height:1px;background:var(--line)"></div>
<div class="copyright">© 2018 All Rights are Reserved. Privacy Policy | Terms of Use</div>

</body>
</html>
```